IT Consulting Business needs a web design

We need a web design for an IT Consulting company called "Vorensk". We want to replace the existing web site (www.vorensk-example.com) with a new design. Our services are IT Consulting, IT Training, IT Outsourcing.
We would like to see designs that communicate "Trusted IT Advisor" with modern & bold design.

We would like to see the design of 2 pages:
1. Home page (www.vorensk-example.com)
2. The detail page (http://www.vorensk-example.com/index_files/consulting.htm)

Industry/Entity Type

Business

```html
<!DOCTYPE html>
<html lang="en">
<head>
<meta charset="utf-8">
<title>Vorensk – IT Consulting</title>
<link href="https://fonts.googleapis.com/css2?family=Roboto:wght@500;700&family=Ubuntu:wght@400;500&display=swap" rel="stylesheet">
<style>
  :root {
    --blue: #1e6fd0;
    --blue-dark: #1258b8;
    --blue-light: #3f95ee;
    --red: #ee1c1c;
    --red-dark: #d20d0d;
    --grey-text: #555;
    --grey-head: #6b6b6b;
    --rule: #dcdcdc;
    --white: #fff;
  }
  * { box-sizing: border-box; margin: 0; padding: 0; }
  html, body { width: 1168px; height: 1200px; overflow: hidden; background: var(--white); }
  body { position: relative; font-family: "Ubuntu", sans-serif; color: var(--grey-text); }

  /* header */
  .site-header { position: absolute; left: 0; top: 0; width: 1168px; height: 72px; border-bottom: 3px solid #d4d4d4; }
  .logo { position: absolute; left: 162px; top: 13px; font-family: "Ubuntu", sans-serif; font-weight: 500; font-size: 34px; color: var(--blue-dark); letter-spacing: -0.5px; }
  .main-nav { position: absolute; left: 533px; top: 0; display: flex; height: 68px; }
  .main-nav a { display: flex; align-items: center; padding: 0 12px; font-size: 12.5px; color: #555; text-decoration: none; border-right: 1px solid #e6e6e6; }
  .main-nav a:last-child { border-right: none; }
  .main-nav a.active { background: var(--blue); color: var(--white); border-top: 4px solid var(--red); padding: 0 14px; border-right: none; }

  /* hero */
  .hero { position: absolute; left: 0; top: 72px; width: 1168px; height: 392px;
    background: radial-gradient(ellipse at 70% 55%, var(--blue-light) 0%, var(--blue) 55%, var(--blue-dark) 100%); }
  .hero-visual { position: absolute; left: 162px; top: 58px; width: 492px; height: 266px; border-radius: 8px;
    background: linear-gradient(180deg, #3a3a3a 0%, #1a1a1a 80%, #cfd3d8 88%, #9aa0a6 100%); }
  .hero-dots { position: absolute; left: 377px; top: 340px; display: flex; gap: 8px; }
  .hero-dots span { width: 15px; height: 15px; border-radius: 50%; background: var(--white); border: 3px solid #123a78; }
  .hero-title { position: absolute; right: 162px; top: 112px; font-family: "Roboto", sans-serif; font-weight: 700; font-size: 21px; color: var(--white); text-align: right; white-space: nowrap; }
  .hero-text { position: absolute; right: 162px; top: 148px; width: 340px; font-size: 12.5px; line-height: 16px; color: var(--white); text-align: right; }

  .btn { position: absolute; display: flex; align-items: center; justify-content: center; width: 73px; height: 28px;
    background: linear-gradient(180deg, #ff3030, var(--red-dark)); color: var(--white); font-size: 12.5px; border-radius: 3px; text-decoration: none; }

  /* core values */
  .core-values { position: absolute; left: 162px; top: 486px; width: 844px; height: 44px; background: var(--blue); }
  .core-shape { position: absolute; left: 0; top: 0; }
  .core-label { position: absolute; left: 15px; top: 12px; font-family: "Roboto", sans-serif; font-weight: 700; font-size: 17px; color: var(--white); }
  .core-item { position: absolute; top: 0; height: 44px; font-family: "Roboto", sans-serif; font-weight: 700; font-size: 13px; color: var(--white); display: flex; align-items: center; gap: 10px; white-space: nowrap; }
  .core-chevron { display: block; flex: none; }

  /* service cards */
  .service-card { position: absolute; top: 558px; width: 257px; text-align: center; }
  .service-photo { width: 257px; height: 105px; border-radius: 4px; }
  .service-card h3 { margin-top: 18px; font-family: "Roboto", sans-serif; font-weight: 500; font-size: 17px; color: var(--grey-head); }
  .service-card p { margin-top: 6px; font-size: 11.5px; line-height: 16px; }
  .col-rule { position: absolute; top: 558px; width: 1px; height: 264px; background: var(--rule); }

  .section-shadow { position: absolute; left: 40px; top: 846px; width: 1088px; height: 8px;
    background: radial-gradient(ellipse at center, rgba(0,0,0,0.07), rgba(0,0,0,0) 70%); }

  /* welcome */
  .section-title { position: absolute; top: 878px; font-family: "Roboto", sans-serif; font-weight: 500; font-size: 17px; color: var(--grey-head); }
  .welcome-photo { position: absolute; left: 162px; top: 909px; width: 257px; height: 119px; border-radius: 4px; }
  .welcome-text { position: absolute; left: 437px; top: 905px; width: 276px; font-size: 11.5px; line-height: 16px; }

  .expertise-list { position: absolute; left: 749px; top: 902px; width: 257px; list-style: none; }
  .expertise-list li { height: 24px; display: flex; align-items: center; gap: 8px; font-size: 11.5px; white-space: nowrap; border-bottom: 1px dotted #cfcfcf; }
  .expertise-list li:last-child { border-bottom: none; }
  .expertise-list svg { flex: none; }

  /* footer */
  .site-footer { position: absolute; left: 0; top: 1096px; width: 1168px; height: 104px; background: var(--blue); color: var(--white); font-size: 12px; }
  .footer-links { position: absolute; left: 161px; top: 20px; display: flex; gap: 8px; }
  .copyright { position: absolute; left: 161px; top: 41px; }
  .contact-line { position: absolute; right: 162px; top: 20px; display: flex; align-items: center; gap: 6px; }
  .social { position: absolute; right: 162px; top: 40px; display: flex; gap: 4px; }
  .social span { width: 23px; height: 23px; border-radius: 50%; background: #0f3f86; }
</style>
</head>
<body>

<header class="site-header">
  <div class="logo">Vorensk</div>
  <nav class="main-nav">
    <a class="active" href="#">HOME</a>
    <a href="#">ABOUT US</a>
    <a href="#">SERVICES</a>
    <a href="#">EXPERTISES</a>
    <a href="#">CAREERS</a>
    <a href="#">CONTACT US</a>
  </nav>
</header>

<section class="hero">
  <div class="hero-visual" role="img" aria-label="Laptop showing a consultant touching a digital world-map interface"></div>
  <div class="hero-dots"><span></span><span></span><span></span></div>
  <h1 class="hero-title">YOUR MOST TRUSTED IT CONSULTANT</h1>
  <p class="hero-text">We are experienced, certified professionals who are experts at Information Technology (IT) consulting, solution design &amp; development, and training for medium-size businesses and large enterprises.</p>
  <a class="btn" href="#" style="left:924px;top:231px;height:30px;">MORE</a>
</section>

<section class="core-values">
  <svg class="core-shape" width="844" height="44" viewBox="0 0 844 44">
    <polygon points="0,0 140,0 162,22 140,44 0,44" fill="#ee1c1c"/>
    <polyline points="140,0 162,22 140,44" fill="none" stroke="#fff" stroke-width="1.5"/>
    <polyline points="360,0 382,22 360,44" fill="none" stroke="#fff" stroke-width="1.5"/>
    <polyline points="586,0 608,22 586,44" fill="none" stroke="#fff" stroke-width="1.5"/>
  </svg>
  <div class="core-label">CORE VALUE</div>
  <div class="core-item" style="left:179px;"><svg class="core-chevron" width="8" height="11" viewBox="0 0 8 11"><polyline points="1,1 6,5.5 1,10" fill="none" stroke="#fff" stroke-width="2.2"/></svg><span>QUALITY CONSCIOUS</span></div>
  <div class="core-item" style="left:416px;"><svg class="core-chevron" width="8" height="11" viewBox="0 0 8 11"><polyline points="1,1 6,5.5 1,10" fill="none" stroke="#fff" stroke-width="2.2"/></svg><span>CUSTOMER FOCUS</span></div>
  <div class="core-item" style="left:659px;"><svg class="core-chevron" width="8" height="11" viewBox="0 0 8 11"><polyline points="1,1 6,5.5 1,10" fill="none" stroke="#fff" stroke-width="2.2"/></svg><span>COMMITTED</span></div>
</section>

<article class="service-card" style="left:162px;">
  <div class="service-photo" role="img" aria-label="Two consultants discussing work at a desk with a monitor" style="background:linear-gradient(135deg,#9fb3c4,#5e6b78 60%,#2f3338);"></div>
  <h3>CONSULTING SERVICES</h3>
  <p>Our experienced, certified professionals provides IT consulting using industry recommended practices. We are specialized in Corvane Business Productivity Platform using Corvane TeamDesk..</p>
</article>
<div class="col-rule" style="left:437px;"></div>
<article class="service-card" style="left:456px;">
  <div class="service-photo" role="img" aria-label="Training session with a presenter at a chart in a meeting room" style="background:linear-gradient(135deg,#e6ecf1,#a9b3bd 55%,#4a5058);"></div>
  <h3>TRAINING SERVICES</h3>
  <p>Our certified trainers provide in-house training for Vorensk original courses as well as customized training courses that suit your organization needs. On-Site training..</p>
</article>
<div class="col-rule" style="left:730px;"></div>
<article class="service-card" style="left:750px;">
  <div class="service-photo" role="img" aria-label="Close-up of a keyboard key labelled Solution" style="background:linear-gradient(135deg,#4d6f9c,#a9bfd8 50%,#5b7aa3);"></div>
  <h3>SOLUTION SERVICES</h3>
  <p>Vorensk's unique solution services offer customers with the benefits of our expert consultants in designing, deploying, and implementing our solutions. Customers who want to have the solution with..</p>
</article>
<a class="btn" href="#" style="left:254px;top:793px;">MORE</a>
<a class="btn" href="#" style="left:548px;top:793px;">MORE</a>
<a class="btn" href="#" style="left:842px;top:793px;">MORE</a>

<div class="section-shadow"></div>

<h2 class="section-title" style="left:162px;">WELCOME TO VORENSK</h2>
<div class="welcome-photo" role="img" aria-label="Two consultants discussing work at a desk with a monitor" style="background:linear-gradient(135deg,#9fb3c4,#5e6b78 60%,#2f3338);"></div>
<p class="welcome-text">We are experienced, certified professionals who are experts at Information Technology (IT) consulting, solution design &amp; development, and training for medium-size businesses and large enterprises. We are committed to helping our clients quickly achieve the most appropriate solution with sustainable ROI. We are focusing on Corvane Technologies for large organizations.</p>
<a class="btn" href="#" style="left:639px;top:1038px;">MORE</a>

<div class="col-rule" style="left:730px;top:874px;height:150px;"></div>

<h2 class="section-title" style="left:749px;">OUR EXPERTISES</h2>
<ul class="expertise-list">
  <li><svg width="8" height="8" viewBox="0 0 8 8"><g fill="#ee1c1c"><rect x="0" y="0" width="3" height="3"/><rect x="5" y="0" width="3" height="3"/><rect x="0" y="5" width="3" height="3"/><rect x="5" y="5" width="3" height="3"/></g></svg>Corvane TeamDesk Technologies</li>
  <li><svg width="8" height="8" viewBox="0 0 8 8"><g fill="#ee1c1c"><rect x="0" y="0" width="3" height="3"/><rect x="5" y="0" width="3" height="3"/><rect x="0" y="5" width="3" height="3"/><rect x="5" y="5" width="3" height="3"/></g></svg>Business Intelligence with Corvane DataCore</li>
  <li><svg width="8" height="8" viewBox="0 0 8 8"><g fill="#ee1c1c"><rect x="0" y="0" width="3" height="3"/><rect x="5" y="0" width="3" height="3"/><rect x="0" y="5" width="3" height="3"/><rect x="5" y="5" width="3" height="3"/></g></svg>Enterprise Integration with LinkBridge Server</li>
  <li><svg width="8" height="8" viewBox="0 0 8 8"><g fill="#ee1c1c"><rect x="0" y="0" width="3" height="3"/><rect x="5" y="0" width="3" height="3"/><rect x="0" y="5" width="3" height="3"/><rect x="5" y="5" width="3" height="3"/></g></svg>StackNet Development</li>
  <li><svg width="8" height="8" viewBox="0 0 8 8"><g fill="#ee1c1c"><rect x="0" y="0" width="3" height="3"/><rect x="5" y="0" width="3" height="3"/><rect x="0" y="5" width="3" height="3"/><rect x="5" y="5" width="3" height="3"/></g></svg>Q7 Ironleaf</li>
</ul>
<a class="btn" href="#" style="left:933px;top:1038px;">MORE</a>

<footer class="site-footer">
  <div class="footer-links">
    <span>Home</span><span>|</span><span>About Us</span><span>|</span><span>Services</span><span>|</span><span>Careers</span><span>|</span><span>Expertises</span><span>|</span><span>Contact Us</span>
  </div>
  <div class="copyright">Vorensk © 2013. All Rights Reserved.</div>
  <div class="contact-line">
    <svg width="14" height="11" viewBox="0 0 14 11"><path d="M1 4 Q7 -1 13 4 L11 5 L10 3.5 L4 3.5 L3 5 Z" fill="#fff"/><rect x="3" y="5" width="8" height="5" rx="1" fill="#fff"/></svg>
    <span>1300 555 019</span>
    <span style="margin:0 4px;">|</span>
    <svg width="14" height="10" viewBox="0 0 14 10"><rect x="0.5" y="0.5" width="13" height="9" fill="none" stroke="#fff"/><polyline points="0.5,0.5 7,6 13.5,0.5" fill="none" stroke="#fff"/></svg>
    <span>info@vorensk-example.com</span>
  </div>
  <div class="social"><span></span><span></span></div>
</footer>

</body>
</html>
```